Local Roofing/Construction company business needs new biz card design

We need a new business card design, current cards are from the start of this operation and generic at best. We are a local Construction Company (General Contractor) with a majority of our work originating from insurance claims-exterior finish work is the main focus (Roofs-Siding-Gutters etc). Heavily involved with homeowners and the low ball offers they receive from insurance company's after a insurable event takes place. I have attached some of our original logo file(s) below.

```html
<!DOCTYPE html>
<html lang="en">
<head>
<meta charset="utf-8">
<title>Trakwell Construction – Business Card</title>
<link href="https://fonts.googleapis.com/css2?family=Montserrat:wght@500;700;800&display=swap" rel="stylesheet">
<style>
  :root {
    --green: #45ad63;
    --green-deep: #349a50;
    --ink: #0b1a1c;
    --grey: #5d6163;
    --card: #f6f6f6;
    --backdrop: #e4e4e4;
  }
  * { box-sizing: border-box; margin: 0; padding: 0; }
  html, body { width: 1200px; height: 1200px; overflow: hidden; }
  body {
    background: var(--backdrop);
    font-family: "Montserrat", sans-serif;
    position: relative;
  }
  .card {
    position: absolute;
    left: 234px;
    width: 731px;
    height: 417px;
    background: var(--card);
    overflow: hidden;
  }
  .card--front { top: 160px; }
  .card--back  { top: 631px; }

  .brand {
    position: absolute;
    display: flex;
    align-items: center;
    gap: 12px;
    color: var(--ink);
    font-weight: 800;
    letter-spacing: 0.5px;
  }
  .brand__name { line-height: 1.05; }
  .brand__square { background: var(--green); flex: none; }
  .card--front .brand { left: 0; right: 0; top: 80px; justify-content: center; font-size: 36px; }
  .card--front .brand__square { width: 78px; height: 78px; }
  .card--back .brand { left: 49px; top: 52px; font-size: 24px; }
  .card--back .brand__square { width: 52px; height: 52px; }

  .specialties { position: absolute; left: 138px; top: 246px; }
  .specialties__title {
    color: var(--green);
    font-weight: 700;
    font-size: 27px;
    letter-spacing: 0.2px;
  }
  .specialties__list {
    list-style: none;
    display: grid;
    grid-template-columns: 257px auto;
    row-gap: 15px;
    margin-top: 20px;
  }
  .specialty {
    display: flex;
    align-items: center;
    gap: 10px;
    color: var(--grey);
    font-weight: 500;
    font-size: 19px;
  }
  .specialty svg { width: 24px; height: 24px; flex: none; }

  .person { position: absolute; right: 66px; top: 54px; text-align: right; }
  .person__name { font-size: 31px; font-weight: 700; color: var(--green); line-height: 1.1; }
  .person__name b { color: var(--ink); }
  .person__role { font-size: 19px; font-weight: 500; color: var(--ink); margin-top: 2px; }

  .contact { position: absolute; left: 49px; top: 242px; list-style: none; }
  .contact li {
    display: flex; align-items: center; gap: 10px;
    font-size: 19px; font-weight: 500; color: var(--grey);
    height: 28px;
  }
  .contact svg { width: 17px; height: 17px; flex: none; }

  .address {
    position: absolute; right: 65px; top: 272px;
    text-align: right; font-style: normal;
    font-size: 19px; font-weight: 500; color: var(--grey); line-height: 26px;
  }
  .swoosh { position: absolute; left: 0; bottom: 0; width: 731px; height: 417px; }
</style>
</head>
<body>

<section class="card card--front">
  <div class="brand"><span class="brand__square"></span><span class="brand__name">TRAKWELL<br>CONSTRUCTION</span></div>
  <div class="specialties">
    <h2 class="specialties__title">OUR CONTRACTING SPECIALTIES</h2>
    <ul class="specialties__list">
      <li class="specialty">
        <svg viewBox="0 0 24 24"><circle cx="12" cy="12" r="12" fill="var(--green)"/><path d="M6 13l6-5 6 5M8 12v5h8v-5" fill="none" stroke="#fff" stroke-width="1.3"/></svg>
        Residential Roofing</li>
      <li class="specialty">
        <svg viewBox="0 0 24 24"><circle cx="12" cy="12" r="12" fill="var(--green)"/><rect x="7" y="7" width="10" height="10" fill="none" stroke="#fff" stroke-width="1.2"/><path d="M7 10.3h10M7 13.7h10M10.3 7v10M13.7 7v10" stroke="#fff" stroke-width="1"/></svg>
        Exterior Finishes</li>
      <li class="specialty">
        <svg viewBox="0 0 24 24"><circle cx="12" cy="12" r="12" fill="var(--green)"/><path d="M7 17V9l5-3 5 3v8zM10 17v-4h4v4" fill="none" stroke="#fff" stroke-width="1.2"/></svg>
        Commercial Roofing</li>
      <li class="specialty">
        <svg viewBox="0 0 24 24"><circle cx="12" cy="12" r="12" fill="var(--green)"/><path d="M7 16h10M8 16a4 4 0 0 1 8 0M9 8l-1 2M12 7v2M15 8l1 2" fill="none" stroke="#fff" stroke-width="1.2"/></svg>
        Storm Restoration</li>
    </ul>
  </div>
</section>

<section class="card card--back">
  <div class="brand"><span class="brand__square"></span><span class="brand__name">TRAKWELL<br>CONSTRUCTION</span></div>
  <div class="person">
    <p class="person__name">Dalton <b>Reese</b></p>
    <p class="person__role">Founder &amp; Director</p>
  </div>
  <ul class="contact">
    <li><svg viewBox="0 0 24 24"><path d="M6 3l4 4-2 3c1.5 3 3 4.5 6 6l3-2 4 4-3 3C10 20 4 14 3 6z" fill="var(--green)"/></svg>555-014-2290</li>
    <li><svg viewBox="0 0 24 24"><rect x="2" y="5" width="20" height="14" fill="var(--green)"/><path d="M2 6l10 7 10-7" fill="none" stroke="#fff" stroke-width="1.6"/></svg>info@trakwellbuilds.com</li>
    <li><svg viewBox="0 0 24 24"><circle cx="12" cy="12" r="9.5" fill="none" stroke="var(--green)" stroke-width="2"/><ellipse cx="12" cy="12" rx="4" ry="9.5" fill="none" stroke="var(--green)" stroke-width="1.8"/><path d="M2.5 12h19" stroke="var(--green)" stroke-width="1.8"/></svg>trakwellbuilds.com</li>
  </ul>
  <address class="address">48 Oak Hollow Ln<br>Fairbrook, MO 63010</address>
  <svg class="swoosh" viewBox="0 0 731 417" preserveAspectRatio="none" aria-hidden="true">
    <path d="M0 386 C250 392 520 370 731 306 V417 H0 Z" fill="var(--green)"/>
    <path d="M0 386 C250 392 520 370 731 306 V417 H0 Z" fill="var(--green-deep)" opacity="0.35"/>
    <path d="M0 334 C180 365 400 372 580 340 C420 380 200 392 0 376 Z" fill="var(--ink)"/>
  </svg>
</section>

</body>
</html>
```